Web Site Design for a Finance (lending) Company

We are opening a new subsidiary that focuses on lending money in the real estate industry. We need a web site designed to represent the business.

The business is lending money to real estate investors. A typical client/borrower will be looking to borrow money to buy a house, renovate it and then sell it at a profit, all within 12 months or less.

Company name is RTV Finance. Our logo is attached.

Attached is a general outline for the web site. We're working on writing more text for each page but this should give you enough to get started with some ideas.

Competitor web site that I like a lot (as an example): https://dorvaleqcapital.example/. Many of the general items on this site match what we will need (description of loan programs, FAQ)

Target Market(s)

Real estate investors (generally individuals or small companies with just a few people) who are buying homes, renovating them and then selling them at a profit.

Industry/Entity Type

Finance

Coding

Coded - Design and coding required

Number of Pages Required

5+ page

Colors

Designer to choose colors to be used in the design.

Requirements
Must have
• Minimalist design. Clean lines without too much clutter. Some stock photography is ok but the photos should not be distracting. They should almost fade in to the background so that user can focus on the key information about what our company does instead. We are a finance company, not a design company, so the information about our products will be more interesting to site visitors than the art.
• Some minimalist examples from Snapboard:
• https://www.snapboardia.example/explore/minimalist-web-design/
Nice to have
• If you search in zoovle for "hard money lenders" you will find many examples of web sites from our competition. I have provided a link above to competitor web site that I like a lot.
• I have attached our logo in EPS format. Logo is green. Web site doesn't have to be green but it should be of a color that will work well with the logo.

```html
<!DOCTYPE html>
<html lang="en">
<head>
<meta charset="utf-8">
<title>RTV Finance</title>
<link rel="stylesheet" href="https://fonts.googleapis.com/css2?family=Roboto:wght@400;500;700&display=swap">
<style>
:root{
  --green:#0b4d33;
  --green-soft:#6b9a80;
  --grey-card:#9c9ea6;
  --grey-soft:#c4c6cb;
  --ink:#222;
  --muted:#555;
  --field:#f1f1f1;
  --field-line:#dcdcdc;
  --black:#000;
  --footer-text:#9a9a9a;
  --white:#fff;
}
*{box-sizing:border-box;margin:0;padding:0}
html,body{width:990px;height:1200px;overflow:hidden}
body{position:relative;background:var(--white);font-family:'Roboto',sans-serif;color:var(--ink)}
.abs{position:absolute}

/* header */
.site-header{position:absolute;left:0;top:0;width:990px;height:82px;background:var(--white)}
.brand{left:80px;top:24px;display:flex;align-items:center;gap:10px}
.brand-mark{width:26px;height:26px;border-radius:50%;background:var(--green)}
.brand-name{font-size:20px;font-weight:500;color:var(--green);line-height:1}
.main-nav a{position:absolute;top:35px;font-size:14px;color:#555;text-decoration:none}
.main-nav a.active{color:var(--green)}
.nav-underline{left:543px;top:79px;width:54px;height:2px;background:var(--green)}
.chat-tab{left:942px;top:38px;width:60px;height:132px;background:#3a3a3a;border-radius:18px 0 0 18px}
.chat-tab span{position:absolute;left:14px;top:40px;writing-mode:vertical-rl;color:var(--white);font-size:12px}
.chat-tab svg{position:absolute;left:17px;top:18px}

/* hero */
.hero{left:0;top:82px;width:990px;height:444px;background:linear-gradient(180deg,#6f9cc8 0%,#a9c7df 40%,#4fa9c4 62%,#3d8a62 85%,#5f8c3f 100%)}
.hero-title{left:80px;top:298px;font-size:27px;font-weight:500;line-height:32px;color:var(--white);text-shadow:0 1px 3px rgba(0,0,0,.4)}
.btn{display:flex;align-items:center;justify-content:center;background:var(--green);color:var(--white);border-radius:20px;font-weight:500}
.hero-btn{left:81px;top:382px;width:142px;height:39px;font-size:14px}
.hero-arrows{left:100px;top:458px}

/* features */
.feature{position:absolute;top:526px;width:206px;height:192px}
.feature-body{height:158px;padding:14px 13px 0;color:var(--white)}
.feature.green .feature-body{background:var(--green)}
.feature.grey .feature-body{background:var(--grey-card)}
.feature p{margin-top:14px;font-size:10.5px;line-height:17px;text-align:justify}
.feature-more{height:34px;display:flex;align-items:center;justify-content:space-between;padding:0 16px;color:var(--white);font-size:11.5px;font-weight:500}
.feature.green .feature-more{background:var(--green-soft)}
.feature.grey .feature-more{background:var(--grey-soft)}

.divider{left:81px;top:734px;width:827px;height:1px;background:#ddd}

/* contact */
.contact-title{left:81px;top:753px;font-size:22px;font-weight:700;color:var(--green)}
.field{position:absolute;height:31px;background:var(--field);border:1px solid var(--field-line);font-size:8.5px;font-weight:500;padding-left:14px;display:flex;align-items:center;color:#222}
.submit-btn{left:81px;top:928px;width:94px;height:34px;font-size:12px}
.contact-info{font-size:14px;color:var(--ink)}
.info-line{left:490px;top:850px;width:418px;height:1px;background:#ddd}

/* footer */
.site-footer{left:0;top:998px;width:990px;height:202px;background:var(--black)}
.partners{position:absolute;left:170px;top:34px;width:640px;display:flex;justify-content:space-between;align-items:center}
.partners span{color:#cfcfcf;font-size:17px;font-weight:500}
.footer-rule{position:absolute;left:81px;width:827px;height:1px;background:#2a2a2a}
.footer-nav a{position:absolute;top:118px;color:var(--footer-text);font-size:13px;text-decoration:none}
.social{position:absolute;top:114px;right:82px;display:flex;gap:12px}
.social span{display:flex;align-items:center;gap:5px;color:var(--footer-text);font-size:10.5px}
.social i{width:8px;height:8px;border:1px solid #777;border-radius:50%}
.copyright{position:absolute;right:84px;top:176px;color:var(--footer-text);font-size:10px}
</style>
</head>
<body>

<header class="site-header">
  <div class="abs brand"><span class="brand-mark"></span><span class="brand-name">RTV Finance</span></div>
  <nav class="main-nav">
    <a class="active" style="left:549px">Home</a>
    <a style="left:612px">About Us</a>
    <a style="left:692px">Loans</a>
    <a style="left:756px">Resources</a>
    <a style="left:845px">Contact Us</a>
  </nav>
  <div class="abs nav-underline"></div>
</header>
<div class="abs chat-tab">
  <svg width="14" height="12" viewBox="0 0 14 12" fill="none" stroke="#fff" stroke-width="1.2"><path d="M2 1h10v7H6l-3 3V8H2z"/></svg>
  <span>Chat Online</span>
</div>

<section class="abs hero" role="img" aria-label="Modern white villa beside a pool with palm trees"></section>
<h1 class="abs hero-title">Local real estate experts lending to<br>local real estate investors</h1>
<div class="abs btn hero-btn">LEARN MORE</div>
<svg class="abs hero-arrows" width="64" height="36" viewBox="0 0 64 36" fill="none" stroke="#fff" stroke-width="1.2"><path d="M18 2 2 18l16 16"/><path d="M46 2l16 16-16 16"/></svg>

<div class="feature green" style="left:81px">
  <div class="feature-body">
    <svg width="56" height="40" viewBox="0 0 56 40" fill="none" stroke="#fff" stroke-width="1.6"><path d="M4 16l10-10 10 4 8-4 14 6 6 10-14 14-10-4-8-6z"/><path d="M20 20l8 8M26 16l8 8M32 14l8 8"/></svg>
    <p>RTV Finance is a local business with local knowledge and strong industry relationships. A partner with a wide network who offers value added services.</p>
  </div>
  <div class="feature-more">READ MORE <span>&#9656;</span></div>
</div>
<div class="feature grey" style="left:288px">
  <div class="feature-body">
    <svg width="50" height="44" viewBox="0 0 50 44" fill="none" stroke="#fff" stroke-width="1.6"><circle cx="16" cy="14" r="12"/><text x="11" y="19" fill="#fff" stroke="none" font-size="14" font-family="Roboto,sans-serif">$</text><path d="M2 34h14l10 4 20-8-6-4-12 4"/></svg>
    <p>RTV has an established pool of experienced investors available for your real estate investment needs</p>
  </div>
  <div class="feature-more">READ MORE <span>&#9656;</span></div>
</div>
<div class="feature green" style="left:495px">
  <div class="feature-body">
    <svg width="44" height="44" viewBox="0 0 44 44" fill="none" stroke="#fff" stroke-width="1.6"><path d="M2 2h20l6 6v32H2z"/><path d="M28 16h12v24H28"/><path d="M8 30l12-14"/><circle cx="9" cy="18" r="2.5"/><circle cx="19" cy="28" r="2.5"/></svg>
    <p style="text-align:left">Loans offere<br>(Fix and Flip, Commercial)</p>
  </div>
  <div class="feature-more">READ MORE <span>&#9656;</span></div>
</div>
<div class="feature grey" style="left:702px">
  <div class="feature-body">
    <svg width="44" height="44" viewBox="0 0 44 44" fill="none" stroke="#fff" stroke-width="1.6"><path d="M2 2h40v10M6 8v34l6-4 6 4 6-4 6 4 6-4V8"/><text x="10" y="28" fill="#fff" stroke="none" font-size="14" font-family="Roboto,sans-serif">$</text><path d="M22 18h10M22 24h10M22 30h10"/></svg>
    <p>Why borrow from RTV (experts, fast approval, professional, a partner, selective, competitive rates and fees)</p>
  </div>
  <div class="feature-more">READ MORE <span>&#9656;</span></div>
</div>

<div class="abs divider"></div>

<h2 class="abs contact-title">CONTACT FORM</h2>
<div class="field" style="left:81px;top:802px;width:201px">FIRST NAME</div>
<div class="field" style="left:290px;top:802px;width:201px">LAST NAME</div>
<div class="field" style="left:81px;top:843px;width:410px">EMAIL</div>
<div class="field" style="left:81px;top:883px;width:410px">HOW YOU HEARD ABOUT US</div>
<div class="abs btn submit-btn">SUBMIT</div>

<svg class="abs" style="left:617px;top:823px" width="14" height="14" viewBox="0 0 14 14"><path d="M3 1l3 3-2 2c1 2 2 3 4 4l2-2 3 3-2 2C6 13 1 8 1 3z" fill="#222"/></svg>
<div class="abs contact-info" style="left:652px;top:821px">Phone&nbsp; : 1800 555 0147</div>
<div class="abs info-line"></div>
<svg class="abs" style="left:614px;top:858px" width="15" height="12" viewBox="0 0 15 12" fill="none" stroke="#222" stroke-width="1.3"><rect x="1" y="1" width="13" height="10"/><path d="M1 1l6.5 6L14 1"/></svg>
<div class="abs contact-info" style="left:652px;top:855px">Email&nbsp; : info@rtvfinance.example</div>

<footer class="abs site-footer">
  <div class="partners">
    <span>Pomelo</span><span>Tradeway</span><span>Gravtek</span><span>Summit Range</span><span>Crimson Ox</span><span>Lensor</span>
  </div>
  <div class="footer-rule" style="top:102px"></div>
  <nav class="footer-nav">
    <a style="left:81px">Home</a>
    <a style="left:144px">About Us</a>
    <a style="left:225px">Loans</a>
    <a style="left:288px">Resources</a>
    <a style="left:377px">Contact Us</a>
  </nav>
  <div class="social">
    <span><i></i>Friendra</span><span><i></i>Chirpo</span><span><i></i>Linkwork</span><span><i></i>Vidstream</span>
  </div>
  <div class="footer-rule" style="top:159px"></div>
  <div class="copyright">© 2017 | www.rtvfinance.example</div>
</footer>

</body>
</html>
```